Business card design needed

I run a Beautician studio (for 7 years now)
I offer
- Velmo Body Sugaring
- Ruby Glaze
- Nails
- Facials
- Manicure
- Foot Treatment
It might not be necessary to list all those treatments?
Maybe the link to the Website is sufficient?
I leave that up to you ...
(more info on www.FernAndDewByLenka.com.au)
Velmo BodySugaring is our biggest success, It replaces waxing.
I would like to incorporate the logo into the Business Card.
We had many complaints regarding our old Business Cards as the Phone Number was to small.
On the backside, we would like a "your next Appointment" section.
Looking forward to you Design, cheers ... Lenka
Industry/Entity Type
Business
Contact Information for Business Card
Fern by Dew by Lenka
14 Korrin Sqr 3942 Berwick
www.FernAndDewByLenka.com.au
03 9481 2267

```html
<!DOCTYPE html>
<html lang="en">
<head>
<meta charset="utf-8">
<title>Velmo Body Sugaring – Business Card</title>
<link rel="stylesheet" href="https://fonts.googleapis.com/css2?family=PT+Sans:wght@400;700&display=swap">
<style>
  :root {
    --backdrop: #3a3a3a;
    --card: #f4f4f3;
    --card-white: #ffffff;
    --ink: #1f1f1f;
    --ink-soft: #3c3c3c;
    --band-dark: #545454;
    --band-light: #7d7d7d;
    --accent: #e8531f;
    --icon-grey: #9a9a9a;
    --sun: #f2a51c;
  }
  * { box-sizing: border-box; margin: 0; padding: 0; }
  html, body {
    width: 1200px;
    height: 949px;
    overflow: hidden;
    background: var(--backdrop);
    font-family: "PT Sans", sans-serif;
  }
  .sheet {
    position: relative;
    width: 1200px;
    height: 949px;
  }
  .card {
    position: absolute;
    left: 250px;
    width: 700px;
    height: 390px;
    box-shadow: 0 10px 28px rgba(0,0,0,0.45);
    overflow: hidden;
  }
  .card--front { top: 50px; background: var(--card); }
  .card--back { top: 510px; background: var(--card-white); }

  /* Front */
  .brand {
    position: absolute;
    left: 95px;
    top: 120px;
    display: flex;
    align-items: center;
    gap: 12px;
  }
  .brand__dot {
    width: 18px;
    height: 18px;
    border-radius: 50%;
    background: var(--sun);
  }
  .brand__name {
    font-size: 26px;
    font-weight: 400;
    letter-spacing: 1px;
    color: var(--ink);
  }
  .contact {
    position: absolute;
    top: 245px;
    left: 0;
    width: 700px;
    height: 56px;
  }
  .contact__address {
    position: absolute;
    right: 390px;
    top: 4px;
    text-align: right;
    font-size: 17px;
    line-height: 24px;
    color: var(--ink);
  }
  .contact__divider {
    position: absolute;
    left: 348px;
    top: 0;
    width: 3px;
    height: 56px;
    background: var(--ink);
  }
  .contact__phone {
    position: absolute;
    left: 372px;
    top: 12px;
    display: flex;
    align-items: center;
    gap: 12px;
    font-size: 26px;
    color: var(--ink);
  }
  .contact__phone svg { width: 30px; height: 30px; }
  .band {
    position: absolute;
    left: 0;
    bottom: 0;
    width: 700px;
    height: 50px;
  }
  .band--front { background: var(--band-dark); }
  .band--back { background: var(--band-light); }
  .band__web {
    position: absolute;
    right: 48px;
    top: 15px;
    font-size: 16px;
    color: var(--card-white);
  }
  .band__accent {
    position: absolute;
    right: 0;
    top: 0;
    width: 30px;
    height: 50px;
    background: var(--accent);
  }

  /* Back */
  .appointment {
    position: absolute;
    left: 70px;
    top: 150px;
    display: flex;
    align-items: center;
    gap: 16px;
  }
  .appointment__rule {
    width: 3px;
    height: 46px;
    background: var(--ink-soft);
  }
  .appointment__label {
    font-size: 24px;
    color: var(--ink);
  }
</style>
</head>
<body>
<main class="sheet">
  <section class="card card--front" aria-label="Business card front">
    <div class="brand">
      <span class="brand__dot"></span>
      <span class="brand__name">Velmo Body Sugaring</span>
    </div>
    <div class="contact">
      <p class="contact__address">Fern by Dew by Lenka<br>14 Korrin Sqr 3942 Berwick</p>
      <span class="contact__divider"></span>
      <p class="contact__phone">
        <svg viewBox="0 0 30 30" aria-hidden="true">
          <circle cx="15" cy="15" r="13" fill="none" stroke="var(--icon-grey)" stroke-width="2"/>
          <path d="M10.5 8.5c1-.6 2-.3 2.5.6l1 2c.4.8.1 1.6-.6 2l-.8.5c.6 1.6 1.8 2.9 3.4 3.6l.5-.8c.5-.7 1.3-.9 2-.5l2 1.1c.9.5 1.1 1.5.5 2.4-1 1.5-2.7 2-4.4 1.2-3.5-1.6-6.2-4.5-7.5-8-.6-1.7-.1-3.2 1.4-4.1z" fill="var(--icon-grey)"/>
        </svg>
        03 9481 2267
      </p>
    </div>
    <div class="band band--front">
      <span class="band__web">www.FernAndDewByLenka.com.au</span>
      <span class="band__accent"></span>
    </div>
  </section>

  <section class="card card--back" aria-label="Business card back">
    <div class="appointment">
      <span class="appointment__rule"></span>
      <span class="appointment__label">Your Next Appointment:</span>
    </div>
    <div class="band band--back"></div>
  </section>
</main>
</body>
</html>
```